Business card for medical clinic

I need an upmarket, modern medical/health business card for my clinic

Contact Information for Business Card

name, address, email, qr code

```html
<!DOCTYPE html>
<html lang="en">
<head>
<meta charset="utf-8">
<title>Meridian Care Partners – Business Card</title>
<link rel="stylesheet" href="https://fonts.googleapis.com/css2?family=Montserrat:wght@400;500;700&display=swap">
<style>
  :root {
    --stage: #1e2935;
    --card-white: #ffffff;
    --brand-navy: #1d4a80;
    --brand-blue: #2a9bd8;
    --ink: #1d2430;
    --back-start: #1f3a5a;
    --back-end: #2598cf;
  }
  * { margin: 0; padding: 0; box-sizing: border-box; }
  html, body {
    width: 1200px; height: 900px; overflow: hidden;
    background: var(--stage);
    font-family: "Montserrat", Arial, sans-serif;
  }
  .canvas { position: relative; width: 1200px; height: 900px; }

  .card {
    position: absolute;
    border-radius: 13px;
    overflow: hidden;
    box-shadow: 0 6px 18px rgba(0,0,0,0.35);
  }

  /* Front */
  .card-front {
    left: 286px; top: 57px; width: 600px; height: 361px;
    background: var(--card-white);
    color: var(--ink);
  }
  .brand {
    position: absolute; display: flex; align-items: center; gap: 12px;
  }
  .brand-mark { border-radius: 50%; flex: none; }
  .brand-name { font-weight: 500; white-space: nowrap; }

  .card-front .brand { left: 28px; top: 84px; max-width: 300px; }
  .card-front .brand-mark { width: 36px; height: 36px; border: 4px solid var(--brand-navy); }
  .card-front .brand-name { font-size: 19px; color: var(--brand-navy); }

  .holder { position: absolute; right: 31px; top: 66px; text-align: right; }
  .holder-name { font-size: 23px; font-weight: 700; color: var(--brand-blue); line-height: 1.1; white-space: nowrap; }
  .holder-title { font-size: 14px; font-weight: 400; color: var(--ink); margin-top: 1px; }
  .accent-bar {
    position: absolute; right: 0; top: 71px; width: 8px; height: 32px;
    background: var(--brand-blue);
  }

  .address {
    position: absolute; left: 30px; top: 226px;
    font-size: 14px; line-height: 16px; font-style: normal;
  }
  .contact-list {
    position: absolute; left: 32px; top: 276px; list-style: none;
    font-size: 14px;
  }
  .contact-list li { display: flex; align-items: center; gap: 10px; height: 18.5px; }
  .contact-list svg { width: 11px; height: 11px; fill: var(--brand-blue); flex: none; }

  /* Back */
  .card-back {
    left: 282px; top: 470px; width: 608px; height: 366px;
    background: linear-gradient(135deg, var(--back-start) 0%, var(--back-end) 100%);
  }
  .card-back .brand { left: 50%; top: 50%; transform: translate(-50%, -50%); gap: 18px; }
  .card-back .brand-mark { width: 52px; height: 52px; border: 5px solid var(--card-white); }
  .card-back .brand-name { font-size: 34px; color: var(--card-white); }
</style>
</head>
<body>
<main class="canvas">

  <section class="card card-front" aria-label="Business card front">
    <div class="brand">
      <span class="brand-mark"></span>
      <span class="brand-name">Meridian Care Partners</span>
    </div>

    <div class="holder">
      <p class="holder-name">Maren Ellsworth</p>
      <p class="holder-title">CEO &amp; Founder</p>
    </div>
    <span class="accent-bar"></span>

    <address class="address">
      248 Harbor View Lane, Suite 310<br>
      Dunmore, PA 18512
    </address>

    <ul class="contact-list">
      <li>
        <svg viewBox="0 0 16 16" aria-hidden="true"><path d="M1 6c0-2 3-3 7-3s7 1 7 3v1h-3V5.5H4V7H1zM4 8h8l2 6H2z"/></svg>
        570-555-0142
      </li>
      <li>
        <svg viewBox="0 0 16 16" aria-hidden="true"><path d="M1 3h14v10H1zM2 4.2v.6l6 4 6-4v-.6l-6 4z"/></svg>
        info@meridiancaregroup.com
      </li>
      <li>
        <svg viewBox="0 0 16 16" aria-hidden="true"><circle cx="8" cy="8" r="7"/><path d="M1 8h14M8 1c3 3 3 11 0 14M8 1c-3 3-3 11 0 14" stroke="#fff" stroke-width="1.2" fill="none"/></svg>
        www.meridiancaregroup.com
      </li>
    </ul>
  </section>

  <section class="card card-back" aria-label="Business card back">
    <div class="brand">
      <span class="brand-mark"></span>
      <span class="brand-name">Meridian Care Partners</span>
    </div>
  </section>

</main>
</body>
</html>
```